Modern card design needed for building development company

We are looking for a sharp modern new look for our business cards.
We are a New Zealand based company called TKR Ventures NZ LTD that specialises in subdividing large sections, housing and commercial buildings.
We have attached a photo of the current logo and would like to see it improved somehow as it looks a bit dated.
We are open to any colours.

Target Market(s)

Investors, Property buyers

Industry/Entity Type

Investment

Contact Information for Business Card

TKR VENTURES NZ LTD
www.tkrventuresnz.co.nz

Damon Whitcombe
Phone +64 21 938 104
Email dpwhitcombe@korumail.co.nz

Font styles to use
Serif
Sans Serif

Colors
0792cd
33a6d7
85cae6
6b449b
886aae
f04a50
ec1f27
f37122
f68d4d

Requirements
Must have
• Please try and make the logo more modern or if you have a similar one we would like to see it.

```html
<!DOCTYPE html>
<html lang="en">
<head>
<meta charset="utf-8">
<title>TKR Ventures NZ LTD – Business Card</title>
<link rel="stylesheet" href="https://fonts.googleapis.com/css2?family=Open+Sans:wght@400;700&display=swap">
<style>
  :root {
    --backdrop: #3a3431;
    --card: #1b1b1b;
    --accent: #f04a50;
    --text: #f2f2f2;
    --muted: #cfcfcf;
  }
  * { box-sizing: border-box; margin: 0; padding: 0; }
  html, body {
    width: 1200px;
    height: 715px;
    overflow: hidden;
    background: var(--backdrop);
    font-family: "Open Sans", Arial, sans-serif;
  }
  .stage {
    position: relative;
    width: 1200px;
    height: 715px;
  }
  .card {
    position: absolute;
    top: 200px;
    width: 530px;
    height: 310px;
    background: var(--card);
    border-radius: 3px;
    box-shadow: 0 10px 30px rgba(0, 0, 0, 0.45);
  }
  .card--front { left: 50px; }
  .card--back { left: 620px; }

  /* Front */
  .front-brand {
    position: absolute;
    inset: 0;
    display: flex;
    align-items: center;
    justify-content: center;
    gap: 14px;
  }
  .brand-square {
    width: 22px;
    height: 22px;
    background: var(--accent);
  }
  .brand-name {
    color: var(--accent);
    font-weight: 700;
    font-size: 26px;
    letter-spacing: 0.5px;
  }

  /* Back */
  .holder {
    position: absolute;
    left: 42px;
    top: 34px;
  }
  .holder-name {
    color: var(--accent);
    font-weight: 700;
    font-size: 17px;
    line-height: 1.2;
  }
  .holder-title {
    color: var(--muted);
    font-size: 10px;
    margin-top: 2px;
  }
  .contact {
    position: absolute;
    left: 42px;
    top: 150px;
    color: var(--text);
    font-size: 12px;
    line-height: 1.55;
    list-style: none;
  }
  .contact-address { margin-bottom: 6px; }
  .contact-line {
    display: flex;
    align-items: center;
    gap: 7px;
  }
  .contact-icon {
    width: 10px;
    height: 10px;
    flex: none;
  }
  .back-brand {
    position: absolute;
    right: 30px;
    bottom: 26px;
    color: var(--accent);
    font-weight: 700;
    font-size: 15px;
    letter-spacing: 1px;
  }
</style>
</head>
<body>
<main class="stage">

  <section class="card card--front" aria-label="Card front">
    <div class="front-brand">
      <span class="brand-square"></span>
      <span class="brand-name">TKR Ventures NZ LTD</span>
    </div>
  </section>

  <section class="card card--back" aria-label="Card back">
    <div class="holder">
      <p class="holder-name">Damon Whitcombe</p>
      <p class="holder-title">Title</p>
    </div>

    <ul class="contact">
      <li class="contact-address">PO BOX 48215<br>Devonport, Auckland, New Zealand</li>
      <li class="contact-line">
        <svg class="contact-icon" viewBox="0 0 10 10" aria-hidden="true">
          <circle cx="5" cy="5" r="5" fill="var(--accent)"/>
          <path d="M3.2 2.6 L4.2 2.4 L4.6 3.8 L4 4.2 Q4.6 5.6 5.8 6 L6.2 5.4 L7.6 5.8 L7.4 6.8 Q4 7 3.2 2.6Z" fill="var(--card)"/>
        </svg>
        64 21 938 104
      </li>
      <li class="contact-line">
        <svg class="contact-icon" viewBox="0 0 10 10" aria-hidden="true">
          <rect x="0.5" y="2" width="9" height="6.5" fill="var(--accent)"/>
          <path d="M0.5 2 L5 5.6 L9.5 2" fill="none" stroke="var(--card)" stroke-width="0.9"/>
        </svg>
        dpwhitcombe@korumail.co.nz
      </li>
      <li class="contact-line">
        <svg class="contact-icon" viewBox="0 0 10 10" aria-hidden="true">
          <circle cx="5" cy="5" r="4.4" fill="none" stroke="var(--accent)" stroke-width="1"/>
          <ellipse cx="5" cy="5" rx="1.8" ry="4.4" fill="none" stroke="var(--accent)" stroke-width="0.8"/>
          <line x1="0.6" y1="5" x2="9.4" y2="5" stroke="var(--accent)" stroke-width="0.8"/>
        </svg>
        www.tkrventuresnz.co.nz
      </li>
    </ul>

    <p class="back-brand">TKR VENTURES NZ LTD</p>
  </section>

</main>
</body>
</html>
```